Elegant Business Card for Technology Company

Client is a supplier of innovative industrial communications and automation equipment since 2002. This contest is to gather fresh ideas for a redesign of the existing business card. Client is looking for design that best communicates tagline "Industrial Networking and Computing Specialist".

Design submissions should look modern, clean, elegant and professional. It should not be cluttered. Use white as the primary colour. Orange and black as secondary colour. Refer to jpeg File 1 on the current design.

Fonts used by Client used include Arial Regular, Arial Black, Roboto Regular, Roboto Black and Lato.

The winning design will be sent for offset printing using super white 250gsm artcard paper (open for suggestions).

Target Market(s)

System Engineers, Project Managers, Purchasing Managers from companies providing engineering services for Smart Cities.

Industry/Entity Type

Information Technology

Contact Information for Business Card

Refer to PDF File 3 for Business Card Details. Priority of short contact information would be as follows Name > Job Title > Email > Mobile > Web > Tel > Fax > Business Address >UEN (UEN represents company registration number)

Font styles to use
Sans Serif

Colors
ffffff
f37122
000000
5c5c5c

Requirements
Must have
• Refer to AI File 2 (Company Logo) & PDF File 3 (Information on Namecard)
Should not have
• No QR codes
• No Social Media Icons
• Do not create full Black or Orange colour background

```html
<!DOCTYPE html>
<html lang="en">
<head>
<meta charset="utf-8">
<title>KVR Business Card</title>
<link href="https://fonts.googleapis.com/css2?family=Source+Sans+3:wght@400;600;700&display=swap" rel="stylesheet">
<style>
  :root {
    --stage: #d8d6d3;
    --card: #ffffff;
    --card-edge: #e2e2e2;
    --orange: #f37122;
    --black: #000000;
    --ink: #1a1a1a;
    --grey: #5c5c5c;
    --rule: #c4c4c4;
  }
  * { box-sizing: border-box; margin: 0; padding: 0; }
  html, body {
    width: 1200px; height: 814px; overflow: hidden;
    background: var(--stage);
    font-family: "Source Sans 3", Arial, sans-serif;
  }
  .canvas {
    width: 1200px; height: 814px;
    display: flex; align-items: center; justify-content: center; gap: 40px;
  }
  .card {
    position: relative;
    width: 540px; height: 324px;
    background: var(--card);
    border: 1px solid var(--card-edge);
    box-shadow: 0 10px 28px rgba(0,0,0,0.18);
    color: var(--ink);
  }

  /* Front */
  .brand {
    display: flex; align-items: center; gap: 10px;
    font-weight: 700; color: var(--black); letter-spacing: 1px;
  }
  .brand-dot { border-radius: 50%; background: var(--orange); flex: none; }
  .front .brand { position: absolute; left: 58px; top: 136px; font-size: 52px; line-height: 1; }
  .front .brand-dot { width: 40px; height: 40px; }
  .divider {
    position: absolute; left: 262px; top: 50px; width: 1px; height: 224px;
    background: var(--rule);
  }
  .contact { position: absolute; left: 282px; top: 58px; font-size: 14px; line-height: 19px; color: var(--grey); }
  .contact-name { color: var(--orange); font-size: 18px; font-weight: 600; line-height: 22px; }
  .contact-title { margin-bottom: 6px; color: var(--ink); }
  .contact-address { margin-bottom: 4px; }
  .contact-list { list-style: none; }
  .contact-list li { display: flex; align-items: center; gap: 8px; height: 20px; }
  .contact-list svg { width: 12px; height: 12px; flex: none; fill: var(--orange); }

  /* Back */
  .back .brand {
    position: absolute; left: 0; right: 0; top: 66px; justify-content: center;
    font-size: 56px; line-height: 1;
  }
  .back .brand-dot { width: 46px; height: 46px; }
  .tagline {
    position: absolute; left: 0; right: 0; top: 172px;
    text-align: center; color: var(--grey); font-size: 14px; line-height: 21px;
  }
</style>
</head>
<body>
<main class="canvas">

  <section class="card front" aria-label="Card front">
    <div class="brand"><span class="brand-dot"></span>KVR</div>
    <div class="divider"></div>
    <div class="contact">
      <p class="contact-name">Daniel Koh</p>
      <p class="contact-title">Sales Manager</p>
      <p class="contact-address">22 Kallang Way<br>Tech Hub #05-12 (Lobby B)<br>Singapore 349301</p>
      <ul class="contact-list">
        <li><svg viewBox="0 0 12 12" aria-hidden="true"><path d="M2.5 0.5 4.5 0.5 5 3.5 3.7 4.4Q4.8 7 7.6 8.3L8.5 7 11.5 7.5 11.5 9.5Q11 11.5 9 11.5 1 10.5 0.5 3 0.5 0.8 2.5 0.5Z"/></svg>+65 6123 4501</li>
        <li><svg viewBox="0 0 12 12" aria-hidden="true"><path d="M3 0h6a1 1 0 0 1 1 1v10a1 1 0 0 1-1 1H3a1 1 0 0 1-1-1V1a1 1 0 0 1 1-1Zm0.5 1.5v7.5h5V1.5Zm2.5 8.3a0.7 0.7 0 1 0 0.01 0Z" fill-rule="evenodd"/></svg>+65 9123 4567</li>
        <li><svg viewBox="0 0 12 12" aria-hidden="true"><path d="M3 0h6v3.5H3ZM0.5 4.5h11v5H9.5V12h-7V9.5h-2ZM3.5 8v3h5V8Z" fill-rule="evenodd"/></svg>+65 6123 4502</li>
        <li><svg viewBox="0 0 12 12" aria-hidden="true"><path d="M0 2h12v8H0Zm1.2 1.2v0.3L6 6.8l4.8-3.3v-0.3Z" fill-rule="evenodd"/></svg>sales@kvr.com.sg</li>
        <li><svg viewBox="0 0 12 12" aria-hidden="true"><circle cx="6" cy="6" r="5.5" fill="none" stroke="#f37122" stroke-width="1.2"/><path d="M0.5 6h11M6 0.5Q2.5 6 6 11.5M6 0.5Q9.5 6 6 11.5" fill="none" stroke="#f37122" stroke-width="1"/></svg>www.kvr.com.sg</li>
      </ul>
    </div>
  </section>

  <section class="card back" aria-label="Card back">
    <div class="brand"><span class="brand-dot"></span>KVR</div>
    <p class="tagline">
      Industrial Networking &amp; Computing Specialist<br>
      Industrial Ethernet / Wireless / Cellular<br>
      Industrial &amp; Embedded Computing / Serial / Fieldbus Connectivity<br>
      IP Video Surveillance / Remote Automation
    </p>
  </section>

</main>
</body>
</html>
```